Business Card Design Project

Business card based on attached logo

Todd Merrick
Todd@lorvantest.com
877-514-9073 ext. 318
Www.LorvanTest.com

Industry/Entity Type

Business

```html
<!DOCTYPE html>
<html lang="en">
<head>
<meta charset="utf-8">
<title>LorvanTest Business Cards</title>
<link rel="stylesheet" href="https://fonts.googleapis.com/css2?family=Arimo:wght@400;700&display=swap">
<style>
  :root {
    --backdrop: #8a8c8f;
    --white: #ffffff;
    --ink: #231f20;
    --red: #e3222a;
    --red-deep: #b81d24;
    --dark: #333333;
    --dark-edge: #1c1c1c;
  }
  * { box-sizing: border-box; margin: 0; padding: 0; }
  html, body {
    width: 1200px; height: 720px; overflow: hidden;
    background: var(--backdrop);
    font-family: "Arimo", Arial, sans-serif;
  }
  .sheet { position: relative; width: 1200px; height: 720px; }
  .card {
    position: absolute; width: 564px; height: 321px;
    border-radius: 24px; overflow: hidden;
    border: 1px solid #555;
  }
  .card--front { left: 24px; top: 27px; background: var(--white); }
  .card--white { left: 609px; top: 27px; background: var(--white); }
  .card--dark {
    left: 24px; top: 372px;
    background: radial-gradient(ellipse at 50% 40%, #4a4a4a 0%, var(--dark) 35%, var(--dark-edge) 100%);
  }
  .card--red {
    left: 609px; top: 372px;
    background: radial-gradient(ellipse at 25% 20%, var(--red) 0%, #d92128 50%, var(--red-deep) 100%);
  }
  .swoosh { position: absolute; inset: 0; width: 100%; height: 100%; }

  .brand { position: absolute; display: flex; align-items: flex-start; gap: 6px; }
  .brand__name {
    font-weight: 700; letter-spacing: -1px; line-height: 1; color: var(--ink);
  }
  .brand__mark { background: var(--red); }
  .brand--light .brand__name { color: var(--white); }
  .brand--light .brand__mark { background: var(--white); }

  .card--front .brand { left: 40px; top: 62px; }
  .card--front .brand__name { font-size: 56px; }
  .card--front .brand__mark { width: 18px; height: 18px; margin-top: -12px; }

  .card--white .brand, .card--dark .brand { left: 50%; transform: translateX(-50%); top: 112px; }
  .card--white .brand__name, .card--dark .brand__name { font-size: 72px; }
  .card--white .brand__mark, .card--dark .brand__mark { width: 24px; height: 24px; margin-top: -16px; }

  .card--red .brand { left: 35px; top: 40px; }
  .card--red .brand__name { font-size: 78px; }

  .holder {
    position: absolute; left: 61px; top: 224px;
    font-size: 19px; line-height: 1; color: var(--red); letter-spacing: 0.3px;
  }
  .contacts {
    position: absolute; right: 13px; top: 222px;
    list-style: none; text-align: right; color: var(--white); font-size: 16.5px;
  }
  .contacts li { height: 27.5px; display: flex; justify-content: flex-end; align-items: center; gap: 7px; }
  .contacts svg { width: 13px; height: 13px; fill: var(--white); }

  .url {
    position: absolute; font-size: 16px; line-height: 1; letter-spacing: 2.6px;
  }
  .card--white .url { left: 0; right: 0; text-align: center; top: 278px; color: var(--ink); }
  .card--dark .url { left: 0; right: 0; text-align: center; top: 279px; color: var(--white); }
  .card--red .url { left: 35px; top: 290px; color: var(--white); }

  .ghost-square {
    position: absolute; right: 0; top: 175px; width: 130px; height: 130px;
    background: rgba(255,255,255,0.12);
  }
</style>
</head>
<body>
<main class="sheet">

  <section class="card card--front">
    <svg class="swoosh" viewBox="0 0 564 321" preserveAspectRatio="none" aria-hidden="true">
      <defs>
        <linearGradient id="redFill" x1="0" y1="1" x2="1" y2="0">
          <stop offset="0" stop-color="#e3222a"/>
          <stop offset="1" stop-color="#a81b22"/>
        </linearGradient>
      </defs>
      <path d="M0,296 C170,292 400,230 564,18 L564,321 L0,321 Z" fill="url(#redFill)"/>
      <path d="M0,262 C90,292 250,272 410,196 C270,262 110,300 0,290 Z" fill="#231f20"/>
      <path d="M0,296 C170,292 400,230 564,18" fill="none" stroke="#ffffff" stroke-width="3"/>
    </svg>
    <div class="brand">
      <span class="brand__name">LorvanTest</span>
      <span class="brand__mark"></span>
    </div>
    <p class="holder">TODD MERRICK</p>
    <ul class="contacts">
      <li><svg viewBox="0 0 16 16"><path d="M4 1l3 3-2 2c1 2 3 4 5 5l2-2 3 3-2 3C7 15 1 9 1 3z"/></svg>877-514-9073 ext. 318</li>
      <li><svg viewBox="0 0 16 16"><path d="M1 4h14v9H1z M1 4l7 5 7-5" /></svg>Todd@lorvantest.com</li>
      <li><svg viewBox="0 0 16 16"><path d="M8 1a7 7 0 100 14A7 7 0 008 1zm0 1.5c1 1 1.7 3 1.8 4.8H6.2C6.3 5.5 7 3.5 8 2.5zM2.6 7.3h2.1c.1-1.6.5-3 1.1-4A5.6 5.6 0 002.6 7.3zm0 1.4a5.6 5.6 0 003.2 4c-.6-1-1-2.4-1.1-4zm3.6 0h3.6c-.1 1.8-.8 3.8-1.8 4.8-1-1-1.7-3-1.8-4.8zm5.1 0c-.1 1.6-.5 3-1.1 4a5.6 5.6 0 003.2-4zm2.1-1.4a5.6 5.6 0 00-3.2-4c.6 1 1 2.4 1.1 4z"/></svg>www.lorvantest.com</li>
    </ul>
  </section>

  <section class="card card--white">
    <div class="brand">
      <span class="brand__name">LorvanTest</span>
      <span class="brand__mark"></span>
    </div>
    <p class="url">www.lorvantest.com</p>
  </section>

  <section class="card card--dark">
    <div class="brand brand--light">
      <span class="brand__name">LorvanTest</span>
      <span class="brand__mark"></span>
    </div>
    <p class="url">www.lorvantest.com</p>
  </section>

  <section class="card card--red">
    <div class="brand brand--light">
      <span class="brand__name">LorvanTest</span>
    </div>
    <span class="ghost-square" aria-hidden="true"></span>
    <p class="url">www.lorvantest.com</p>
  </section>

</main>
</body>
</html>
```